Life Coaching Business Card

Please check out my website at www.lorettavanbrekel.example. Ideally I would like to use the same colors that I used on the site to match my business cards i.e: pink, green, teal, white
I want the final design to include a picture of me and also to be appealing and eye catching. For the picture I submitted, you can crop it smaller to just have my face (exclude my chest) showing.
Business
Contact Information for Business Card
Loretta Vanbrekel
Transformational Life Coach
web: www.lorettavanbrekel.example
email: loretta@lorettavanbrekel.example
Phone: 555-318-7062

```html
<!DOCTYPE html>
<html lang="en">
<head>
<meta charset="utf-8">
<title>Loretta Vanbrekel – Business Card</title>
<link rel="stylesheet" href="https://fonts.googleapis.com/css2?family=Josefin+Slab:ital,wght@0,300;0,400;0,600;0,700;1,400&display=swap">
<style>
  :root {
    --lime: #adff00;
    --pink: #ff1ad6;
    --teal: #5ff3ea;
    --white: #ffffff;
    --panel-edge: #e9e9eb;
    --ink: #111111;
    --photo-light: #bdbdbd;
    --photo-dark: #2a2a2a;
  }
  html, body {
    margin: 0;
    padding: 0;
    overflow: hidden;
    background: var(--white);
  }
  .card {
    position: relative;
    width: 1200px;
    height: 686px;
    overflow: hidden;
    background: var(--lime);
    font-family: "Josefin Slab", Georgia, serif;
    color: var(--ink);
  }
  .card-shapes {
    position: absolute;
    inset: 0;
  }
  .text {
    position: absolute;
    margin: 0;
    white-space: nowrap;
    line-height: 1;
  }
  .specialty-heading {
    left: 280px;
    width: 920px;
    text-align: center;
    top: 48px;
    font-size: 41px;
    font-style: italic;
    font-weight: 400;
    color: var(--white);
  }
  .specialty {
    font-size: 31px;
    font-weight: 400;
    color: var(--white);
    line-height: 1.3;
  }
  .specialty-couples { left: 537px; top: 132px; }
  .specialty-disability { left: 794px; top: 132px; }
  .person-name {
    left: 66px;
    top: 478px;
    font-size: 47px;
    font-weight: 700;
    letter-spacing: 1px;
  }
  .person-title {
    left: 66px;
    top: 550px;
    font-size: 32px;
    font-weight: 300;
    color: var(--white);
    letter-spacing: 0.5px;
  }
  .contact {
    left: 658px;
    font-weight: 400;
    letter-spacing: 0.5px;
  }
  .contact-phone { top: 328px; font-size: 34px; }
  .contact-web { top: 460px; font-size: 30px; }
  .contact-email { top: 602px; font-size: 27px; }
</style>
</head>
<body>
<div class="card">
  <svg class="card-shapes" width="1200" height="686" viewBox="0 0 1200 686" aria-hidden="false">
    <defs>
      <linearGradient id="panelFade" x1="0" y1="0" x2="1" y2="0">
        <stop offset="0" stop-color="var(--white)"/>
        <stop offset="1" stop-color="var(--panel-edge)"/>
      </linearGradient>
      <radialGradient id="portraitTone" cx="0.45" cy="0.4" r="0.7">
        <stop offset="0" stop-color="var(--photo-light)"/>
        <stop offset="1" stop-color="var(--photo-dark)"/>
      </radialGradient>
    </defs>

    <!-- colour bands -->
    <rect class="band-pink" x="280" y="40" width="920" height="185" fill="var(--pink)"/>
    <rect class="band-teal" x="0" y="225" width="470" height="192" fill="var(--teal)"/>

    <!-- contact panel -->
    <rect class="contact-panel" x="642" y="395" width="558" height="291" fill="url(#panelFade)"/>
    <path class="contact-tab" d="M610 295 H1200 V395 H610 A50 50 0 0 1 610 295 Z" fill="url(#panelFade)"/>
    <path class="contact-tab" d="M610 425 H780 V525 H610 A50 50 0 0 1 610 425 Z" fill="var(--white)"/>
    <path class="contact-tab" d="M610 566 H780 V666 H610 A50 50 0 0 1 610 566 Z" fill="var(--white)"/>

    <!-- portrait ring -->
    <circle class="portrait-ring" cx="286" cy="229" r="190" fill="var(--teal)"/>
    <path class="portrait-ring-pink" d="M152 363 A190 190 0 0 1 420 95 Z" fill="var(--pink)"/>
    <circle class="portrait" cx="286" cy="229" r="178" fill="url(#portraitTone)" role="img" aria-label="Black and white portrait photo of Loretta Vanbrekel"/>

    <!-- specialty bullets -->
    <g class="bullet" transform="translate(499 151)">
      <circle r="19" fill="var(--white)"/>
      <path d="M-13.4 13.4 A19 19 0 0 1 13.4 -13.4 Z" fill="var(--ink)"/>
    </g>
    <g class="bullet" transform="translate(752 151)">
      <circle r="19" fill="var(--white)"/>
      <path d="M-13.4 13.4 A19 19 0 0 1 13.4 -13.4 Z" fill="var(--ink)"/>
    </g>

    <!-- name underline -->
    <rect class="name-rule" x="51" y="533" width="235" height="3" fill="var(--pink)"/>
    <rect class="name-rule" x="286" y="533" width="245" height="2" fill="var(--teal)"/>

    <!-- phone icon -->
    <path class="icon-phone" fill="var(--ink)" d="M594 322 l9 -4 l8 14 l-7 5 c2 8 6 14 12 19 l6 -6 l13 9 l-4 9 c-3 4 -9 4 -14 1 c-12 -8 -21 -21 -26 -35 c-2 -5 -1 -10 3 -12 Z"/>

    <!-- globe icon -->
    <g class="icon-globe" fill="none" stroke="var(--ink)" stroke-width="3.5" transform="translate(613 476)">
      <circle r="20" fill="var(--ink)"/>
      <ellipse rx="8" ry="20" stroke="var(--white)" stroke-width="2.5"/>
      <line x1="-20" y1="0" x2="20" y2="0" stroke="var(--white)" stroke-width="2.5"/>
      <line x1="-17" y1="-9" x2="17" y2="-9" stroke="var(--white)" stroke-width="2.5"/>
      <line x1="-17" y1="9" x2="17" y2="9" stroke="var(--white)" stroke-width="2.5"/>
    </g>

    <!-- envelope icon -->
    <g class="icon-mail" transform="translate(590 601)">
      <rect width="56" height="36" fill="var(--ink)"/>
      <path d="M2 2 L28 22 L54 2" fill="none" stroke="var(--white)" stroke-width="2.5"/>
      <path d="M2 34 L22 17 M54 34 L34 17" fill="none" stroke="var(--white)" stroke-width="2"/>
    </g>
  </svg>

  <p class="text specialty-heading">Specializing in</p>
  <p class="text specialty specialty-couples">couples</p>
  <p class="text specialty specialty-disability">individuals experiencing<br>disability in their lives</p>

  <h1 class="text person-name">Loretta Vanbrekel</h1>
  <p class="text person-title">Transformational Life Coach</p>

  <p class="text contact contact-phone">(555)-318-7062</p>
  <p class="text contact contact-web">www.lorettavanbrekel.example</p>
  <p class="text contact contact-email">loretta@lorettavanbrekel.example</p>
</div>
</body>
</html>
```